Redesign of business card for Cedar Ridge Mechanical

We are looking for a new design for our business cards for Cedar Ridge Mechanical. We are a plumbing & HVAC construction company, operating on the West Coast of Canada and USA. Logo attached.
Industry/Entity Type
Construction - Plumbing & HVAC
Contact Information for Business Card
Name, address, phone numbers, email, website address
Look and feel
Each slider illustrates characteristics of the customer's brand and the style your logo design should communicate.

```html
<!DOCTYPE html>
<html lang="en">
<head>
<meta charset="utf-8">
<title>Cedar Ridge Mechanical – Business Card</title>
<link href="https://fonts.googleapis.com/css2?family=Montserrat:wght@400;700&family=Saira+Condensed:wght@700&display=swap" rel="stylesheet">
<style>
  :root {
    --page-bg: #1c1c1e;
    --card-bg: #111112;
    --card-edge: #232325;
    --ink: #ffffff;
    --ink-soft: #e6e6e6;
    --pattern-a: #151516;
    --pattern-b: #1f1f21;
  }
  * { margin: 0; padding: 0; box-sizing: border-box; }
  html, body {
    width: 1200px; height: 963px; overflow: hidden;
    background: var(--page-bg);
  }
  .sheet {
    width: 1200px; height: 963px;
    display: flex; flex-direction: column; align-items: center; justify-content: center;
    gap: 56px;
  }
  .card {
    position: relative;
    width: 700px; height: 400px;
    border-radius: 22px;
    background: var(--card-bg);
    border: 1px solid var(--card-edge);
    overflow: hidden;
    box-shadow: 0 18px 40px rgba(0,0,0,.45);
  }

  /* Front */
  .card-front { display: flex; align-items: center; }
  .brand {
    width: 330px; padding-left: 56px;
    display: flex; align-items: center; gap: 14px;
  }
  .brand-square {
    width: 22px; height: 22px; flex: none;
    background: var(--ink);
  }
  .brand-name {
    font-family: "Montserrat", sans-serif;
    font-weight: 700; font-size: 25px; line-height: 1.15;
    letter-spacing: .04em; text-transform: uppercase;
    color: var(--ink);
  }
  .divider {
    width: 1px; height: 196px; background: var(--ink-soft); flex: none;
  }
  .contact {
    padding-left: 34px;
    font-family: "Montserrat", sans-serif;
    color: var(--ink);
  }
  .contact-name { font-weight: 700; font-size: 23px; letter-spacing: .03em; text-transform: uppercase; }
  .contact-role { font-size: 16px; margin-bottom: 14px; color: var(--ink-soft); }
  .contact-address { font-size: 17px; line-height: 1.25; margin-bottom: 14px; }
  .contact-list { list-style: none; font-size: 17px; line-height: 1.45; }
  .contact-list li { display: flex; align-items: center; gap: 9px; }
  .contact-list svg { width: 15px; height: 15px; flex: none; }

  /* Back */
  .card-back { display: flex; align-items: flex-start; justify-content: flex-end; }
  .back-texture {
    position: absolute; inset: 0;
    background: linear-gradient(135deg, var(--pattern-b), var(--pattern-a) 55%, var(--pattern-b));
  }
  .back-name {
    position: relative;
    margin: 44px 48px 0 0;
    font-family: "Saira Condensed", sans-serif;
    font-weight: 700; font-size: 48px; letter-spacing: .06em;
    text-transform: uppercase; color: var(--ink);
    white-space: nowrap;
  }
</style>
</head>
<body>
<main class="sheet">
  <section class="card card-front" aria-label="Business card front">
    <div class="brand">
      <span class="brand-square"></span>
      <span class="brand-name">Cedar Ridge<br>Mechanical</span>
    </div>
    <div class="divider"></div>
    <div class="contact">
      <p class="contact-name">Daniel Reyes</p>
      <p class="contact-role">Manager</p>
      <p class="contact-address">Your address, city<br>state, ZIP 0000</p>
      <ul class="contact-list">
        <li>
          <svg viewBox="0 0 16 16" aria-hidden="true"><path fill="#fff" d="M3.6 1.5l2.3 2.6-1.2 1.6c.9 2 2.4 3.5 4.5 4.6l1.6-1.2 2.7 2.2-1.2 2.4C7.3 13.5 2.6 8.8 2.1 3z"/></svg>
          <span>555-310-4827</span>
        </li>
        <li>
          <svg viewBox="0 0 16 16" aria-hidden="true"><rect x="1.5" y="3.5" width="13" height="9" fill="none" stroke="#fff" stroke-width="1.4"/><path d="M1.5 3.5L8 9l6.5-5.5" fill="none" stroke="#fff" stroke-width="1.4"/></svg>
          <span>youremail@cedarmail.com</span>
        </li>
        <li>
          <svg viewBox="0 0 16 16" aria-hidden="true"><circle cx="8" cy="8" r="6.5" fill="none" stroke="#fff" stroke-width="1.3"/><ellipse cx="8" cy="8" rx="2.8" ry="6.5" fill="none" stroke="#fff" stroke-width="1.1"/><path d="M1.5 8h13" stroke="#fff" stroke-width="1.1"/></svg>
          <span>www.yourwebsite.com</span>
        </li>
      </ul>
    </div>
  </section>

  <section class="card card-back" aria-label="Business card back">
    <div class="back-texture" role="img" aria-label="Faint repeating brand pattern across the card background"></div>
    <p class="back-name">Cedar Ridge Mechanical</p>
  </section>
</main>
</body>
</html>
```